Biz Card Design TVCP

New business card for a new company.
Logo was completed by a designer on ArtHarbor and looking to continue requesting additional services.
Company Name: Tidal Vector Power Consulting
Although this company is starting in Canada, we will be moving towards a global presence within the next 6 months.
Key elements to this business are as follows.
Energy Procurement
Energy Reduction Services
Demand Side Consulting
Energy Efficiency Consulting
Saving Clients Money
Helping Them Go "Green"
Managing Their Energy Requirements
Basically the goal for our company is to find the best procurement solution for our clients and reduce their energy consumption. This reduces their expenses and the amount of greenhouse gas they produce on a daily basis.
I have been in the energy footprint for the last 20 years and know that most companies are looking to "do whatever is necessary to get them to sign on the dotted line". I would prefer to walk away from a client that I can't help than to put them into a situation that they will regret for years to come. This is where the "TIDAL" part of the company name comes from.
The following is a catch phrase that encompasses what we do.
"Reducing your carbon footprint & energy bill at the same time!"
The back of the card needs to have this statement along with some sort of illustration. The back is a playground for creative ideas.
The front of the card needs the following.
Logo.
First & Last Name (Gus Marwick)
Title (Energy Warrior)
Phone Number (555) 314-2718
Fax Number (555) 271-8314
Email Address gus@tidalvectorpowerconsulting.example
Address 47 fenwick rd Toronto Ontario K4T 2P9
I want it to be a card that is remembered when any of my staff give it to a customer. It HAS to stand out.
Target Market(s)
Business Owners, Decision Makers, 30 to 65+
Industry/Entity Type
Business
Look and feel

```html
<!DOCTYPE html>
<html lang="en">
<head>
<meta charset="utf-8">
<title>Tidal Vector Power Consulting — Business Card</title>
<link rel="stylesheet" href="https://fonts.googleapis.com/css2?family=Exo+2:wght@700&family=Arimo:wght@400;700&display=swap">
<style>
  :root {
    --stage: #3b3b3b;
    --card: #050505;
    --brand-blue: #3f74c9;
    --brand-green: #1fae4b;
    --leaf-green: #5bcf63;
    --text-white: #f2f2f2;
    --text-soft: #cfcfcf;
  }
  * { margin: 0; padding: 0; box-sizing: border-box; }
  html, body { width: 1200px; height: 900px; overflow: hidden; }
  body {
    background: var(--stage);
    display: flex;
    align-items: center;
    justify-content: center;
    gap: 40px;
    font-family: "Arimo", Arial, sans-serif;
  }
  .card {
    position: relative;
    width: 540px;
    height: 309px;
    background: var(--card);
    box-shadow: 0 12px 30px rgba(0,0,0,0.45);
    overflow: hidden;
  }
  .brand-mark {
    display: block;
    border-radius: 50%;
    background: var(--leaf-green);
    margin: 0 auto;
  }
  .wordmark {
    font-family: "Exo 2", "Arial Black", sans-serif;
    font-weight: 700;
    color: var(--brand-blue);
    text-align: center;
    white-space: nowrap;
    letter-spacing: -0.2px;
  }

  /* back of card */
  .card-back {
    display: flex;
    flex-direction: column;
    align-items: center;
    justify-content: center;
  }
  .card-back .brand-mark { width: 110px; height: 110px; margin-bottom: 22px; }
  .card-back .wordmark { font-size: 31px; }
  .tagline {
    margin-top: 8px;
    font-size: 12.5px;
    color: var(--text-white);
    text-align: center;
  }

  /* front of card */
  .card-front {
    display: flex;
    flex-direction: column;
    align-items: center;
    padding: 48px 40px 0 22px;
  }
  .card-front .brand-mark { width: 52px; height: 52px; margin-bottom: 10px; }
  .card-front .wordmark { font-size: 25px; }
  .person-name {
    margin-top: 14px;
    font-size: 15px;
    color: var(--brand-green);
  }
  .person-title {
    margin-top: 3px;
    font-size: 9px;
    color: var(--text-soft);
  }
  .contact-line {
    margin-top: 18px;
    font-size: 9.5px;
    color: var(--text-white);
    white-space: nowrap;
  }
  .contact-line .label { color: var(--brand-green); font-weight: 700; }
  .contact-line .label.fax { color: var(--brand-blue); }
  .contact-line .item + .item { margin-left: 8px; }
  .address {
    margin-top: 6px;
    font-size: 11px;
    color: var(--text-white);
  }
  .edge-stripe {
    position: absolute;
    top: 0; right: 0;
    width: 16px;
    height: 100%;
    display: flex;
    flex-direction: column;
  }
  .edge-stripe span { display: block; }
  .edge-stripe .green { background: var(--brand-green); }
  .edge-stripe .blue { background: var(--brand-blue); }
</style>
</head>
<body>
  <section class="card card-back" aria-label="Business card back">
    <span class="brand-mark" aria-hidden="true"></span>
    <p class="wordmark">TidalVectorPowerConsulting</p>
    <p class="tagline">Reducing your carbon footprint &amp; energy bill at the same time!</p>
  </section>

  <section class="card card-front" aria-label="Business card front">
    <span class="brand-mark" aria-hidden="true"></span>
    <p class="wordmark">TidalVectorPowerConsulting</p>
    <p class="person-name">Gus Marwick</p>
    <p class="person-title">Energy Warrior</p>
    <p class="contact-line">
      <span class="item"><span class="label">P:</span> (555) 314-2718</span>
      <span class="item"><span class="label fax">F:</span> (555) 271-8314</span>
      <span class="item"><span class="label">E:</span> gus@tidalvectorpowerconsulting.example</span>
    </p>
    <p class="address">47 fenwick rd Toronto Ontario K4T 2P9</p>
    <div class="edge-stripe" aria-hidden="true">
      <span class="green" style="height:14%"></span>
      <span class="blue" style="height:14%"></span>
      <span class="green" style="height:30%"></span>
      <span class="blue" style="height:12%"></span>
      <span class="green" style="height:30%"></span>
    </div>
  </section>
</body>
</html>
```